TA BRAMLEY BUSINESS CARD DESIGN PROJECT

We need to utilize our logo that was expertly created on PixelHarbor and now need to match this with a business card design.

```html
<!DOCTYPE html>
<html lang="en">
<head>
<meta charset="utf-8">
<title>TA BRAMLEY Business Card</title>
<link rel="stylesheet" href="https://fonts.googleapis.com/css2?family=Montserrat:wght@400;500;700&display=swap">
<style>
  :root {
    --brand-blue: #0f57ad;
    --card-black: #161616;
    --page-bg: #2b2b2d;
    --text-light: #e9e9e9;
    --text-muted: #c9c9c9;
  }
  * { box-sizing: border-box; margin: 0; padding: 0; }
  html, body {
    width: 1200px; height: 780px; overflow: hidden;
    background: var(--page-bg);
    font-family: "Montserrat", Arial, sans-serif;
  }
  .stage {
    position: relative; width: 1200px; height: 780px;
    display: flex; align-items: center; justify-content: center; gap: 44px;
  }
  .card {
    position: relative; width: 530px; height: 310px;
    border-radius: 24px; overflow: hidden;
    box-shadow: 0 18px 40px rgba(0,0,0,.45);
  }
  /* Back card */
  .card--back { background: var(--card-black); }
  .card__wave { position: absolute; left: 0; bottom: 0; width: 530px; height: 110px; }
  .card__brand {
    position: absolute; left: 34px; top: 70px; width: 200px;
    display: flex; align-items: center; gap: 10px;
  }
  .brand-mark {
    width: 16px; height: 16px; border-radius: 50%;
    background: var(--brand-blue); flex: none;
  }
  .brand-name {
    color: var(--brand-blue); font-weight: 700; font-size: 25px;
    letter-spacing: 2px; line-height: 1;
  }
  .card__divider {
    position: absolute; left: 252px; top: 36px;
    width: 1.5px; height: 170px; background: var(--brand-blue);
  }
  .contact { position: absolute; left: 272px; top: 38px; color: var(--text-light); }
  .contact__name {
    color: var(--brand-blue); font-weight: 700; font-size: 19px; letter-spacing: .5px;
  }
  .contact__role { font-size: 13.5px; margin: 2px 0 10px; }
  .contact__list { list-style: none; font-size: 12.5px; }
  .contact__list li { display: flex; align-items: center; gap: 7px; margin-bottom: 4px; }
  .contact__list svg { width: 12px; height: 12px; fill: var(--brand-blue); flex: none; }
  .contact__address { font-size: 12.5px; margin-top: 6px; line-height: 1.4; color: var(--text-muted); }
  /* Front card */
  .card--front {
    background: var(--brand-blue);
    display: flex; align-items: center; justify-content: center; gap: 16px;
  }
  .card--front .brand-mark { width: 26px; height: 26px; background: #fff; }
  .card--front .brand-name { color: #fff; font-size: 48px; letter-spacing: 5px; }
</style>
</head>
<body>
<main class="stage">
  <section class="card card--back" aria-label="Business card back">
    <svg class="card__wave" viewBox="0 0 530 110" preserveAspectRatio="none" aria-hidden="true">
      <path d="M0 60 C120 20 220 95 330 80 C420 68 480 70 530 110 L0 110 Z" fill="var(--brand-blue)"/>
      <path d="M0 44 C120 4 220 80 330 66 C420 54 480 56 530 96" fill="none" stroke="var(--brand-blue)" stroke-width="3"/>
    </svg>

    <div class="card__brand">
      <span class="brand-mark"></span>
      <span class="brand-name">TA BRAMLEY</span>
    </div>

    <div class="card__divider"></div>

    <div class="contact">
      <p class="contact__name">ELENA MARSH</p>
      <p class="contact__role">Managing Director</p>
      <ul class="contact__list">
        <li><svg viewBox="0 0 24 24"><path d="M6.6 10.8a15.1 15.1 0 0 0 6.6 6.6l2.2-2.2c.3-.3.7-.4 1-.2 1.1.4 2.3.6 3.6.6.6 0 1 .4 1 1V20c0 .6-.4 1-1 1A17 17 0 0 1 3 4c0-.6.4-1 1-1h3.5c.6 0 1 .4 1 1 0 1.3.2 2.5.6 3.6.1.3 0 .7-.2 1z"/></svg>123 456 789</li>
        <li><svg viewBox="0 0 24 24"><path d="M7 2h10a2 2 0 0 1 2 2v16a2 2 0 0 1-2 2H7a2 2 0 0 1-2-2V4a2 2 0 0 1 2-2zm0 3v12h10V5zm5 13.5a1.2 1.2 0 1 0 0 2.4 1.2 1.2 0 0 0 0-2.4z"/></svg>123 456 789</li>
        <li><svg viewBox="0 0 24 24"><path d="M2 5h20v14H2zm2 2v.5l8 5 8-5V7l-8 5z"/></svg>info@yourmail.com</li>
        <li><svg viewBox="0 0 24 24"><path d="M12 2a10 10 0 1 0 0 20 10 10 0 0 0 0-20zm6.9 6h-3a15 15 0 0 0-1.3-3.9A8 8 0 0 1 18.9 8zM12 4c.9 1.2 1.6 2.5 2 4h-4c.4-1.5 1.1-2.8 2-4zM4.3 14a8 8 0 0 1 0-4h3.4a16 16 0 0 0 0 4zm.8 2h3a15 15 0 0 0 1.3 3.9A8 8 0 0 1 5.1 16zm3-8h-3a8 8 0 0 1 4.3-3.9A15 15 0 0 0 8.1 8zM12 20c-.9-1.2-1.6-2.5-2-4h4c-.4 1.5-1.1 2.8-2 4zm2.3-6H9.7a14 14 0 0 1 0-4h4.6a14 14 0 0 1 0 4zm.3 5.9c.6-1.2 1-2.5 1.3-3.9h3a8 8 0 0 1-4.3 3.9zm1.7-5.9a16 16 0 0 0 0-4h3.4a8 8 0 0 1 0 4z"/></svg>www.yourwebsite.com</li>
      </ul>
      <p class="contact__address">Your address, City<br>State, Zip 1234</p>
    </div>
  </section>

  <section class="card card--front" aria-label="Business card front">
    <span class="brand-mark"></span>
    <span class="brand-name">TA BRAMLEY</span>
  </section>
</main>
</body>
</html>
```